Design letter head and business card

Hello,

you should design a business card and letter paper for Kranichflug Marketing. In German we write this word with K insteat of C.

Company does not have a logo. But in general, we write Kranichflug Marketing in 2 lines.
First line red: KRANICHFLUG
Second line gray: MARKETING

Red (or wine red) and Gray / Black are our favorite colors.

Company slogan: "Fresh Ground Online Marketing".

Company offers SEO, SEM, SEA, AdWords, Conversion Optimization, Online Markting Consulting ...

The website is old, please do not use this as base for your task.

German letter paper sizes:
Viawable Dimensions : 210 x 297 mm
Needed file dimensions: 212 x 299 mm

Informations to include:

Address:
Kranichflug Marketing GmbH
Lindenweg 23
73614 Rebhausen
Germany

Geschäftsführer | CEO: Bernhard Olzner

Phone: +49 (0) 7382 846 27 05

Fax: +49 (0) 7382 846 27 88

Mail: info@kranichflug-beispiel.de

Web: www.kranichflug-beispiel.de

Amtsgericht Suttgart, HRB 537264

Bank: Rosenauer Bank
IBAN: DE827315480900XXXXXXXX
BIC: RSNBDEX1RSQ

Thanks

Bernhard

Target Market(s)

People who likes to win the online marketing game.

Industry/Entity Type

Business

Contact Information for Business Card

Here is the personal text on the card:

Name:
Bernhard Olzner

Title:
Geschäftsführer | CEO

Address:
Kranichflug Marketing GmbH
Lindenweg 23
73614 Rebhausen
Germany

Phone:
+49 (0) 7382 846 27 05

Fax:
+49 (0) 7382 846 27 88

Mail:
olzner@kranichflug-beispiel.de

Web:
www.kranichflug-beispiel.de

Business Card:
Viewable Dimensions: 85 x 55 mm
Needed file dimensions: 87 x 57mm

Font styles to use
Sans Serif

Requirements
Nice to have
• It would be great to see the dynamics of a helicopter.

```html
<!DOCTYPE html>
<html lang="de">
<head>
<meta charset="utf-8">
<title>Kranichflug Marketing – Geschäftsausstattung</title>
<link href="https://fonts.googleapis.com/css2?family=Questrial&display=swap" rel="stylesheet">
<style>
  :root {
    --red: #b8102e;
    --grey: #6e6e6e;
    --dark: #3c3c3c;
    --dark-edge: #333333;
    --paper: #f6f6f6;
    --ink: #3a3a3a;
    --stage: #d3d3d3;
    --white: #ffffff;
  }
  * { box-sizing: border-box; margin: 0; padding: 0; }
  html, body { width: 1200px; height: 900px; overflow: hidden; }
  body { background: var(--stage); font-family: "Questrial", "Century Gothic", sans-serif; color: var(--ink); }
  .canvas { position: relative; width: 1200px; height: 900px; }

  .sheet { position: absolute; background: var(--paper); }
  .bands { position: absolute; top: 0; left: 0; right: 0; display: flex; gap: 3px; }
  .bands .band-red { flex: 1; background: var(--red); }
  .bands .band-grey { flex: 1; background: var(--grey); }

  /* Company name: one colour, one weight, plain square beside it */
  .company-name { position: absolute; display: flex; align-items: center; gap: 0.4em; line-height: 1; color: var(--red); white-space: nowrap; }
  .company-name .mark-square { display: inline-block; width: 0.6em; height: 0.6em; background: var(--red); }

  /* Letterhead */
  .letterhead { left: 220px; top: 54px; width: 382px; height: 540px; }
  .letterhead .bands { height: 7px; }
  .letterhead .company-name { left: 35px; top: 42px; font-size: 15px; }
  .letterhead .slogan { position: absolute; right: 35px; top: 44px; font-size: 9.5px; color: var(--ink); }
  .letter-body { position: absolute; left: 36px; top: 110px; width: 311px; font-size: 5.2px; line-height: 1.35; color: #555; }
  .letter-body .date { margin-bottom: 10px; }
  .letter-body .recipient { margin-bottom: 32px; }
  .letter-body .salutation { font-weight: bold; color: var(--ink); margin-bottom: 8px; }
  .letter-body p { margin-bottom: 8px; text-align: justify; }
  .signoff { display: flex; align-items: flex-start; gap: 8px; margin-top: 10px; }
  .signoff strong { color: var(--ink); }
  .signature-area { width: 80px; height: 34px; background: linear-gradient(90deg, #eef0f6, #e2e6f2); margin-top: -10px; }
  .fold-mark { position: absolute; left: 0; width: 18px; height: 1px; background: #cfcfcf; }
  .letter-footer { position: absolute; left: 36px; right: 36px; bottom: 14px; display: flex; justify-content: space-between; font-size: 4.9px; line-height: 1.45; color: #555; }
  .contact-line { display: flex; align-items: center; gap: 3px; }
  .icon { display: inline-block; width: 5px; height: 5px; border-radius: 1px; background: var(--red); }
  .bank { font-size: 4.2px; }

  /* Folder */
  .folder { position: absolute; left: 650px; top: 40px; width: 415px; height: 553px; background: linear-gradient(180deg, #404040, #383838); border-radius: 3px; }
  .folder .spine { position: absolute; left: 26px; top: 0; bottom: 0; width: 2px; background: var(--dark-edge); }
  .folder .company-name { left: 100px; top: 110px; font-size: 24px; }
  .folder .slogan { position: absolute; left: 162px; top: 495px; font-size: 12.5px; }

  .slogan-lead { color: var(--white); }
  .slogan-tail { color: var(--red); }

  /* Business cards */
  .card { position: absolute; left: 78px; width: 164px; height: 91px; }
  .card-front { top: 638px; background: var(--paper); }
  .card-front .bands { height: 4px; gap: 2px; }
  .card-front .company-name { left: 8px; top: 46px; font-size: 6.6px; }
  .card-front .divider { position: absolute; left: 88px; top: 24px; width: 1px; height: 52px; background: #d6d6d6; }
  .card-details { position: absolute; left: 92px; top: 22px; font-size: 3.7px; line-height: 1.4; color: #555; }
  .card-details .person { color: var(--red); font-weight: bold; font-size: 4.6px; }
  .card-details .contact-line .icon { width: 3.5px; height: 3.5px; }
  .card-details .postal { margin-top: 5px; }
  .card-back { top: 747px; height: 92px; background: var(--dark); }
  .card-back .company-name { left: 32px; top: 36px; font-size: 9.5px; }
  .card-back .slogan { position: absolute; left: 48px; top: 73px; font-size: 4.8px; }

  /* Envelopes */
  .envelope { position: absolute; top: 639px; width: 400px; height: 200px; background: var(--paper); }
  .envelope-front { left: 278px; }
  .envelope-front .bands { height: 7px; }
  .envelope-front .company-name { left: 23px; top: 36px; font-size: 15px; }
  .envelope-front .sender { position: absolute; left: 23px; top: 70px; font-size: 5.2px; line-height: 1.35; color: #555; }
  .envelope-back { left: 724px; }
  .envelope-back svg { position: absolute; left: 0; top: 0; }
  .envelope-back .web { position: absolute; left: 0; right: 0; top: 27px; text-align: center; font-size: 5.5px; color: var(--white); }
</style>
</head>
<body>
<main class="canvas">

  <section class="sheet letterhead">
    <div class="bands"><span class="band-red"></span><span class="band-grey"></span></div>
    <div class="company-name"><span class="mark-square"></span>Kranichflug Marketing</div>
    <div class="slogan">Fresh Ground Online Marketing</div>
    <span class="fold-mark" style="top:190px"></span>
    <span class="fold-mark" style="top:380px"></span>
    <div class="letter-body">
      <div class="date">30.02.2015</div>
      <div class="recipient">Recipient's name<br>Gartenstr. 8<br>10119 Berlin<br>Germany</div>
      <div class="salutation">Dear sir,</div>
      <p>A clear letter carries the voice of a company. It shows care, order and respect for the reader, and it leaves a lasting mark long after a screen has gone dark.</p>
      <p>In a world of quick messages and short chats, printed words still hold weight. They are kept, filed and read again, and they speak for the sender in every room they enter.</p>
      <p>Every line should suit the moment and the person who reads it. Good structure, plain language and a calm tone make even complex ideas easy to follow.</p>
      <p>Writing a good letter is a craft. With a solid base and a little practice, anyone can shape a message that feels personal and clear.</p>
      <div class="signoff">
        <div>Yours Sincerely,<br><strong>Lena Wasmer</strong></div>
        <div class="signature-area" role="img" aria-label="Handwritten signature"></div>
      </div>
    </div>
    <footer class="letter-footer">
      <div>Lindenweg 23<br>73614 Rebhausen, Germany</div>
      <div>
        <div class="contact-line"><span class="icon"></span>+49 (0) 7382 846 27 05</div>
        <div class="contact-line"><span class="icon"></span>+49 (0) 7382 846 27 88</div>
      </div>
      <div>
        <div class="contact-line"><span class="icon"></span>info@kranichflug-beispiel.de</div>
        <div class="contact-line"><span class="icon"></span>www.kranichflug-beispiel.de</div>
      </div>
      <div class="bank">Bank: Rosenauer Bank<br>IBAN: DE827315480900XXXXXXXX<br>BIC: RSNBDEX1RSQ</div>
    </footer>
  </section>

  <section class="folder">
    <span class="spine"></span>
    <div class="company-name"><span class="mark-square"></span>Kranichflug Marketing</div>
    <div class="slogan"><span class="slogan-lead">Fresh Ground</span> <span class="slogan-tail">Online Marketing</span></div>
  </section>

  <section class="card card-front">
    <div class="bands"><span class="band-red"></span><span class="band-grey"></span></div>
    <div class="company-name"><span class="mark-square"></span>Kranichflug Marketing</div>
    <span class="divider"></span>
    <div class="card-details">
      <div class="person">BERNHARD OLZNER</div>
      <div>Managing Director</div>
      <div class="contact-line" style="margin-top:3px"><span class="icon"></span>+49 (0) 7382 846 27 05</div>
      <div class="contact-line"><span class="icon"></span>+49 (0) 7382 846 27 88</div>
      <div class="contact-line"><span class="icon"></span>olzner@kranichflug-beispiel.de</div>
      <div class="contact-line"><span class="icon"></span>www.kranichflug-beispiel.de</div>
      <div class="postal">Lindenweg 23<br>73614 Rebhausen, Germany</div>
    </div>
  </section>

  <section class="card card-back">
    <div class="company-name"><span class="mark-square"></span>Kranichflug Marketing</div>
    <div class="slogan"><span class="slogan-lead">Fresh Ground</span> <span class="slogan-tail">Online Marketing</span></div>
  </section>

  <section class="envelope envelope-front">
    <div class="bands"><span class="band-red"></span><span class="band-grey"></span></div>
    <div class="company-name"><span class="mark-square"></span>Kranichflug Marketing</div>
    <div class="sender">Lindenweg 23<br>73614 Rebhausen<br>Germany</div>
  </section>

  <section class="envelope envelope-back">
    <svg width="400" height="60" viewBox="0 0 400 60" aria-hidden="true">
      <polygon points="0,0 400,0 385,56 15,56" fill="#3c3c3c"/>
    </svg>
    <div class="web">www.kranichflug-beispiel.de</div>
  </section>

</main>
</body>
</html>
```